Postcard for our major fundraising event - KindlingJOY2018

Bright Harbor KIDS Camp (BHK) and Youth Summit Trail Camp (YSTC) are ministries of Lindell Fellowship Church that serve Ventura County children of abuse, abandonment and neglect living in foster care. We are looking for a postcard design to promote our single largest fundraising event of the year, GatheringJOY2018, to raise awareness and support for children of abuse. GatheringJOY is a dinner banquet on at an exclusive outdoor venue, "Willow Hollow" with a rustic, ranch feel and with spectacular panoramic views of the City of Camarillo. The event will include music, refreshments, appetizers, a Santa Maria-style barbeque (BBQ), coffee and dessert, testimonials from camp, prize drawings, an opportunity to partner with BHK and YSTC, and time to socialize before and after.
Updates

I have just uploaded text copy to help designers come closer to what we are looking for. Thank you very much for your interest! -Rob

Target Market(s)

People from both within and from outside our sponsoring church who have a heart for hurting children and who are willing and able to financially support our camping (BHK & YSTC) ministries.

Industry/Entity Type

Church

Font styles to use
Serif
Decorative
Script

Requirements
Must have
• Name: GatheringJOY2018... raising awareness and support for children of abuse
• Date: Thursday, May 24, 2018, 6:30-8:00 pm
• Place: Willow Hollow at Dunmore Ranch, 2715 Barlow Lane, Somis, California.
• Cost: $30 per person
• Tickets: Available at Tixlane.com
• Front side should include the elements of the event (although not necessarily bulleted like below):
• • Social hour
• • Music
• • Hors d’eourves
• • Refreshments
• • Santa Maria-style BBQ dinner
• • Coffee & dessert
• • Prize drawings
• • Stories from camp
• See attachment for suggested copy for back side.
• BHK and YSTC logos should be included on the postcard. I’ve uploaded a variety of photos for the designer to choose from; they do not necessarily all have to be included. There are also lots more pics available on our Facebook (Bright Harbor KIDS of Ventura).
• The front-side of the postcard can be entirely images and text. The back-side of the post card should include our return address at the top left ("BHK/YSTC of Lindell Fellowship Church, 418 Kestrel Ridge Way, Ventura, CA 93017") and should leave at least the right half of the postcard clear for addressing and postage.
• BHK colors are purple (Pantone 267) and red (Pantone 186). YSTC colors are green and yellow.
Nice to have
• A selection of camp photos large enough to easily view, but no so many that they are too small to identify. And, perhaps, a design element that evokes a rustic, outdoors, western, ranch feel, but not so much that it seems that we are promoting a country hoedown.
Should not have
• Anything sexual or sensual, related to alcoholic beverages, gambling, guns, or anything negative.

```html
<!DOCTYPE html>
<html lang="en">
<head>
<meta charset="utf-8">
<title>GatheringJOY 2018 Postcard</title>
<link rel="stylesheet" href="https://fonts.googleapis.com/css2?family=Crete+Round&family=Oswald:wght@400;500&family=Berkshire+Swash&display=swap">
<style>
:root{
  --bg:#e6e6e6;
  --purple:#38286a;
  --purple-dark:#2a1d52;
  --wood-light:#8a6545;
  --wood:#6e4d33;
  --wood-dark:#4e3522;
  --cream:#f5f0de;
  --paper:#f3efdd;
  --ink-gray:#666;
}
*{margin:0;padding:0;box-sizing:border-box}
html,body{width:956px;height:1200px;overflow:hidden;background:var(--bg)}
.stage{position:absolute;left:0;top:0;width:1068px;height:1343px;transform:scale(0.8935);transform-origin:0 0}
.card{position:absolute;left:110px;width:865px;height:557px;overflow:hidden;box-shadow:0 3px 8px rgba(0,0,0,.3)}
.card--front{top:95px;background:linear-gradient(180deg,var(--wood-light),var(--wood) 55%,var(--wood-dark))}
.card--back{top:710px;background:#fff}
.abs{position:absolute}
.photo{position:absolute}
.hero-photo{left:0;top:0;width:865px;height:275px;background:linear-gradient(180deg,#4d6a3a 0%,#33402f 35%,#3b4a3f 70%,#5a6b4a 100%)}
.foliage{right:0;top:0;width:260px;height:557px;background:linear-gradient(90deg,rgba(70,110,40,0),rgba(80,120,45,.8) 40%,rgba(60,95,35,.9))}
.polaroid{position:absolute;background:var(--paper);padding:10px 10px 18px;box-shadow:0 2px 6px rgba(0,0,0,.35)}
.polaroid .shot{width:100%;height:100%}
.banner{position:absolute;background:var(--purple);color:var(--cream);font-family:"Crete Round",serif;display:flex;align-items:center;justify-content:center;white-space:nowrap}
.banner-stub{position:absolute;background:var(--purple-dark)}
.banner-tail{position:absolute}
.cond{font-family:"Oswald",sans-serif;color:var(--cream);line-height:1.05;letter-spacing:-.3px}
.script{font-family:"Berkshire Swash",cursive;color:var(--cream);text-align:center}
.icon-box{position:absolute;width:40px;height:40px;background:var(--purple);border:2px solid var(--cream);display:flex;align-items:center;justify-content:center}
.tagline{left:32px;top:340px;font-size:22px;font-weight:500;text-transform:uppercase}
.info{font-size:20px}
.links{left:36px;top:516px;width:570px;font-size:16.5px;letter-spacing:-.4px;display:flex;align-items:center;gap:6px;white-space:nowrap}
.dot{display:inline-block;width:13px;height:13px;border-radius:50%;background:var(--cream);margin-left:10px}
.back-wood{left:0;top:0;width:438px;height:557px;background:linear-gradient(180deg,var(--wood-light),var(--wood) 50%,var(--wood-dark))}
.back-leaves{left:0;top:0;width:438px;height:40px;background:linear-gradient(180deg,rgba(90,130,50,.85),rgba(90,130,50,0))}
.brand-row{left:0;top:62px;width:438px;display:flex;justify-content:center;gap:34px}
.brand{display:flex;align-items:center;gap:7px;font-family:"Oswald",sans-serif;font-size:15px;color:var(--cream);font-weight:500;white-space:nowrap}
.brand .mark{width:28px;height:28px;border-radius:50%;background:var(--cream);flex:none}
.centered{left:0;width:438px;text-align:center}
.rule-row{display:flex;align-items:center;justify-content:center;gap:10px}
.rule-row .rule{height:1px;width:70px;background:var(--cream)}
.return-address{left:490px;top:45px;font-family:"Oswald",sans-serif;font-size:12.5px;color:var(--ink-gray);line-height:1.75}
.stamp-box{left:733px;top:30px;width:95px;height:66px;border:1px solid #aaa}
.small{font-size:12.5px;line-height:1.2}
</style>
</head>
<body>
<div class="stage">

  <section class="card card--front">
    <div class="photo hero-photo" role="img" aria-label="Campers paddling green canoes across a tree-lined lake"></div>
    <div class="photo foliage" role="img" aria-label="Green leafy branches along the right edge"></div>

    <div class="polaroid" style="left:625px;top:12px;width:228px;height:160px;transform:rotate(4deg)">
      <div class="shot" role="img" aria-label="Camper and counselor practicing archery on a grassy field" style="background:linear-gradient(180deg,#5d7a3f,#7fa34a)"></div>
    </div>
    <div class="polaroid" style="left:617px;top:205px;width:228px;height:145px;transform:rotate(-4deg)">
      <div class="shot" role="img" aria-label="Children splashing and playing in a swimming pool" style="background:linear-gradient(180deg,#9a7b5c,#3fa6c2)"></div>
    </div>
    <div class="polaroid" style="left:630px;top:380px;width:223px;height:165px;transform:rotate(4deg)">
      <div class="shot" role="img" aria-label="Campers on a trail ride on horseback" style="background:linear-gradient(180deg,#4f6e3a,#b9a888)"></div>
    </div>

    <div class="banner-stub" style="left:0;top:273px;width:18px;height:70px"></div>
    <svg class="banner-tail" style="left:538px;top:275px" width="82" height="72" viewBox="0 0 82 72"><polygon points="0,0 82,0 62,36 82,72 0,72" fill="#2a1d52"/></svg>
    <div class="banner" style="left:18px;top:262px;width:530px;height:70px;font-size:46px">★ GatheringJOY 2018 ★</div>

    <div class="abs cond tagline">Raising awareness and support for children of abuse</div>

    <div class="icon-box" style="left:32px;top:375px">
      <svg width="24" height="24" viewBox="0 0 24 24" fill="none" stroke="#f5f0de" stroke-width="2"><rect x="3" y="5" width="18" height="16"/><line x1="3" y1="10" x2="21" y2="10"/><line x1="8" y1="2" x2="8" y2="7"/><line x1="16" y1="2" x2="16" y2="7"/></svg>
    </div>
    <div class="abs cond info" style="left:80px;top:374px">Thursday, May 24, 2018,<br>6:30-8:00 pm</div>

    <div class="icon-box" style="left:293px;top:377px">
      <svg width="24" height="24" viewBox="0 0 24 24"><path d="M12 2a7 7 0 0 0-7 7c0 5 7 13 7 13s7-8 7-13a7 7 0 0 0-7-7z" fill="#f5f0de"/><circle cx="12" cy="9" r="2.6" fill="#38286a"/></svg>
    </div>
    <div class="abs cond info" style="left:342px;top:377px">Willow Hollow at Dunmore Ranch,<br>2715 Barlow Lane, Somis, California.</div>

    <div class="icon-box" style="left:32px;top:433px">
      <svg width="24" height="24" viewBox="0 0 24 24"><path d="M3 12 12 3h9v9l-9 9z" fill="#f5f0de"/><circle cx="16.5" cy="7.5" r="1.6" fill="#38286a"/></svg>
    </div>
    <div class="abs cond info" style="left:80px;top:442px">$30 per person</div>

    <div class="icon-box" style="left:293px;top:435px">
      <svg width="24" height="24" viewBox="0 0 24 24"><rect x="2" y="7" width="20" height="11" rx="1" fill="#f5f0de"/><line x1="15" y1="7" x2="15" y2="18" stroke="#38286a" stroke-dasharray="2 2"/></svg>
    </div>
    <div class="abs cond info" style="left:342px;top:444px">Available at Tixlane.com</div>

    <div class="abs script" style="left:20px;top:480px;width:590px;font-size:14px;line-height:1.1">Social Hour • Music • Hors D'eourves • Refreshments • Santa Maria-style BBQ Dinner<br>Coffee &amp; Dessert • Prize Drawings • Stories From Camp</div>

    <div class="abs cond links">
      <svg width="14" height="14" viewBox="0 0 24 24" fill="none" stroke="#f5f0de" stroke-width="2"><circle cx="12" cy="12" r="10"/><ellipse cx="12" cy="12" rx="4" ry="10"/><line x1="2" y1="12" x2="22" y2="12"/></svg>
      <span>ventura.brightharborkids.org | youthsummittrail.org</span>
      <span class="dot"></span>
      <span>Bright Harbor KIDS of Ventura</span>
    </div>
  </section>

  <section class="card card--back">
    <div class="abs back-wood"></div>
    <div class="abs back-leaves" role="img" aria-label="Leafy branches hanging along the top edge"></div>

    <div class="abs brand-row">
      <div class="brand"><span class="mark"></span>Bright Harbor KIDS</div>
      <div class="brand"><span class="mark"></span>Youth Summit</div>
    </div>

    <div class="abs cond centered" style="top:135px;font-size:19px">Bright Harbor KIDS Camp &amp; Youth Summit Trail Camp</div>
    <div class="abs cond centered" style="top:158px;font-size:14px">of Lindell Fellowship Church</div>
    <div class="abs cond centered rule-row" style="top:177px;font-size:16px"><span class="rule"></span>INVITE YOU TO JOIN US FOR<span class="rule"></span></div>

    <div class="banner-stub" style="left:0;top:215px;width:18px;height:58px"></div>
    <svg class="banner-tail" style="left:400px;top:218px" width="58" height="58" viewBox="0 0 58 58"><polygon points="0,0 58,0 42,29 58,58 0,58" fill="#2a1d52"/></svg>
    <div class="banner" style="left:18px;top:205px;width:385px;height:60px;font-size:36px">★ GatheringJOY 2018 ★</div>

    <div class="abs script centered" style="top:266px;font-size:15px">Raising awareness and Support for children of abuse</div>

    <div class="abs cond centered" style="top:296px;font-size:14px">at the exclusive</div>
    <div class="abs cond centered" style="top:315px;font-size:19px">Willow Hollow at Dunmore Ranch</div>
    <div class="abs cond centered" style="top:338px;font-size:19px">2715 Barlow Lane, Somis, CA</div>
    <div class="abs cond centered rule-row" style="top:364px;font-size:14px"><span class="rule"></span>on<span class="rule"></span></div>
    <div class="abs cond centered" style="top:385px;font-size:19px">Thursday, May 24, 2018</div>
    <div class="abs cond centered" style="top:408px;font-size:19px">6:30-8:00 pm</div>

    <div class="polaroid" style="left:2px;top:345px;width:100px;height:88px;transform:rotate(-5deg);padding:7px 7px 12px">
      <div class="shot" role="img" aria-label="Young camper in a helmet riding a bicycle" style="background:linear-gradient(180deg,#5c7445,#8a8f7a)"></div>
    </div>
    <div class="polaroid" style="left:335px;top:315px;width:135px;height:112px;transform:rotate(5deg);padding:7px 7px 12px">
      <div class="shot" role="img" aria-label="Camper on a ropes course beside a camp banner among pine trees" style="background:linear-gradient(180deg,#8fb0c9,#3f5f33)"></div>
    </div>

    <div class="abs cond centered small" style="top:443px">Tickets $30 per person/Available at Tixlane.com<br>All proceeds to benefit BHKC &amp; YSTC serving children of abuse ages 7-14.</div>
    <div class="abs cond centered small" style="top:490px">For more information:<br>BHKC: Director Rob Haverly (805) 555-0142 / bhkcventura@mailbox.net<br>YSTC: Director Dale Perrin (805) 555-0187 / daleperrinphoto@mailbox.net</div>

    <div class="abs return-address">BHK/YSTC of Lindell Fellowship Church,<br>418 Kestrel Ridge Way, Ventura, CA 93017</div>
    <div class="abs stamp-box"></div>
  </section>

</div>
</body>
</html>
```